SOLVE Study flyer

I need help designing a flyer for a research study that will include brain imaging in adolescents. The info is in the attached document. The study is called the Sequoia Outlook Lantern Valley Echo (SOLVE) study. Ideally this would be returned as a document that I can edit in the future as we will have several new recruitment phases (different age groups, etc. I also would love to have a logo designed as part of this project, but I recognize that might be a separate design request.

```html
<!DOCTYPE html>
<html lang="en">
<head>
<meta charset="utf-8">
<title>SOLVE Study Flyer</title>
<link rel="stylesheet" href="https://fonts.googleapis.com/css2?family=Poppins:wght@400;500;600;700;800&display=swap">
<style>
  :root {
    --navy: #0b1f6e;
    --royal: #0a3fc2;
    --gold: #fbb816;
    --ink: #3a3a3a;
    --white: #ffffff;
  }
  * { margin: 0; padding: 0; box-sizing: border-box; }
  html, body { width: 902px; height: 1200px; overflow: hidden; background: var(--white); }
  body { font-family: "Poppins", sans-serif; color: var(--navy); }
  .flyer { position: relative; width: 902px; height: 1200px; background: var(--white); }

  .study-name { position: absolute; left: 80px; top: 52px; font-size: 21px; font-weight: 700; line-height: 27px; }
  .study-name .accent { color: var(--royal); }
  .study-title { position: absolute; left: 78px; top: 130px; font-size: 52px; font-weight: 800; letter-spacing: -0.5px; color: var(--navy); }

  .question-band { position: absolute; left: 72px; top: 210px; width: 400px; height: 150px; }
  .question-band svg { position: absolute; inset: 0; }
  .question { position: absolute; left: 36px; display: flex; align-items: center; gap: 10px; color: var(--white); font-size: 15.5px; line-height: 20px; }
  .question b { font-weight: 700; }
  .q-icon { width: 33px; height: 33px; border-radius: 6px; background: var(--gold); color: var(--white); font-weight: 800; font-size: 26px; display: flex; align-items: center; justify-content: center; flex: none; }

  .brain-photo { position: absolute; left: 448px; top: 102px; width: 400px; height: 365px; border-radius: 48% 52% 45% 50% / 52% 50% 48% 46%; background: radial-gradient(ellipse at 45% 40%, #f3b79a 0%, #e09172 55%, #c8674c 100%); }

  .intro { position: absolute; left: 85px; top: 388px; width: 370px; font-size: 14.4px; line-height: 18.5px; color: var(--ink); }

  .section-title { position: absolute; left: 80px; top: 488px; font-size: 30px; font-weight: 700; }
  .section-title .accent { color: var(--royal); }

  .steps { position: absolute; left: 80px; top: 558px; display: flex; gap: 14px; }
  .step { width: 239px; height: 304px; background: var(--navy); color: var(--white); text-align: center; padding: 18px 24px 0; font-size: 16px; font-weight: 600; line-height: 20px; }
  .step.highlight { background: var(--royal); }
  .step svg { display: block; margin: 0 auto 20px; }
  .step .accent { color: var(--gold); }

  .kids-photo { position: absolute; left: 78px; top: 892px; width: 322px; height: 190px; border-radius: 40px 40px 20px 20px; background: linear-gradient(160deg, #d0453f 0%, #e9b64a 40%, #3f69c1 75%, #2e3a66 100%); }

  .eligible-title { position: absolute; left: 411px; top: 888px; font-size: 25px; font-weight: 700; }
  .eligible-title .accent { color: var(--royal); }
  .criteria { position: absolute; left: 414px; top: 932px; list-style: none; font-size: 16px; color: var(--ink); line-height: 20px; }
  .criteria li { display: flex; gap: 8px; margin-bottom: 7px; }
  .criteria b { font-weight: 700; }
  .tick { width: 15px; height: 15px; flex: none; margin-top: 3px; }

  .compensation { position: absolute; left: 417px; top: 1052px; width: 408px; height: 42px; }
  .compensation svg { position: absolute; inset: 0; }
  .compensation span { position: relative; display: block; text-align: center; line-height: 42px; font-size: 18px; font-weight: 700; letter-spacing: 4px; color: var(--navy); }

  .contact-bar { position: absolute; left: 80px; top: 1108px; width: 743px; height: 35px; display: flex; font-size: 13.5px; font-weight: 700; }
  .contact-bar .prompt { background: var(--navy); color: var(--white); flex: 1; display: flex; align-items: center; padding-left: 12px; gap: 6px; }
  .contact-bar .prompt .accent { color: var(--gold); }
  .contact-bar .email { background: var(--royal); color: var(--white); width: 199px; display: flex; align-items: center; padding-left: 8px; font-size: 11.5px; }
</style>
</head>
<body>
<main class="flyer">
  <h2 class="study-name"><span class="accent">Sequoia</span><br>Outlook <span class="accent">Lantern</span><br><span class="accent">Valley</span> Echo</h2>
  <h1 class="study-title">SOLVE study</h1>

  <div class="question-band">
    <svg width="400" height="150" viewBox="0 0 400 150" preserveAspectRatio="none" aria-hidden="true">
      <polygon fill="#0b1f6e" points="2,8 20,4 40,7 60,2 80,6 100,3 120,7 140,2 160,6 180,3 200,8 220,4 240,7 260,3 280,6 300,9 320,5 340,8 360,6 380,9 400,7 400,140 380,146 360,142 340,147 320,143 300,148 280,144 260,149 240,144 220,147 200,143 180,148 160,144 140,147 120,143 100,148 80,144 60,147 40,143 20,148 2,144 6,120 1,95 7,70 2,45 6,25"/>
    </svg>
    <div class="question" style="top:32px"><span class="q-icon">?</span><span>Are you the parent of a child<br><b>age 10-17?</b></span></div>
    <div class="question" style="top:86px"><span class="q-icon">?</span><span>Do they worry or overthink<br><b>negative emotions?</b></span></div>
  </div>

  <div class="brain-photo" role="img" aria-label="Photograph of an anatomical human brain model"></div>

  <p class="intro">Northfield University researchers are seeking girls age 10-17 for a study about brain activity in emotions and decision-making and how they relate to puberty, anxiety and depression.</p>

  <h2 class="section-title">Study participation <span class="accent">involves</span></h2>

  <section class="steps">
    <div class="step">
      <svg width="50" height="50" viewBox="0 0 50 50" fill="#fbb816" aria-hidden="true">
        <rect x="12" y="2" width="26" height="14" rx="7"/>
        <circle cx="25" cy="22" r="5"/><path d="M17 38 a8 8 0 0 1 16 0z"/>
        <circle cx="11" cy="27" r="4"/><path d="M4 40 a7 7 0 0 1 14 0z"/>
        <circle cx="39" cy="27" r="4"/><path d="M32 40 a7 7 0 0 1 14 0z"/>
        <rect x="2" y="40" width="46" height="8" rx="1"/>
      </svg>
      One one-hour interview <span class="accent">(online or in-person)</span> where your child will discuss their thoughts
    </div>
    <div class="step highlight">
      <svg width="50" height="50" viewBox="0 0 50 50" fill="none" stroke="#fbb816" stroke-width="3" aria-hidden="true">
        <rect x="5" y="14" width="34" height="24" rx="2"/>
        <path d="M1 44 h48" stroke-width="4"/>
        <circle cx="18" cy="24" r="4" fill="#fbb816"/><path d="M11 35 a7 6 0 0 1 14 0z" fill="#fbb816"/>
        <rect x="30" y="2" width="18" height="12" rx="2" fill="#fbb816" stroke="none"/>
      </svg>
      Online questionnaires <span class="accent">(parent and child)</span>
    </div>
    <div class="step">
      <svg width="50" height="50" viewBox="0 0 50 50" fill="#fbb816" aria-hidden="true">
        <rect x="8" y="2" width="14" height="11" rx="2"/><circle cx="35" cy="8" r="6"/>
        <circle cx="11" cy="22" r="4"/><circle cx="39" cy="22" r="4"/>
        <path d="M4 40 v-10 a7 7 0 0 1 14 0 v10z"/><path d="M32 40 v-10 a7 7 0 0 1 14 0 v10z"/>
        <rect x="14" y="30" width="22" height="4"/><rect x="23" y="34" width="4" height="14"/>
      </svg>
      One two-hour visit where your child will complete an MRI scan, answer questions about their puberty stage, and have a small hair sample taken to study puberty hormones
    </div>
  </section>

  <div class="kids-photo" role="img" aria-label="Photograph of a group of smiling children sitting together"></div>

  <h2 class="eligible-title">Your child may be eligible <span class="accent">if they</span></h2>
  <ul class="criteria">
    <li><svg class="tick" viewBox="0 0 16 16" aria-hidden="true"><circle cx="8" cy="8" r="8" fill="#fbb816"/><path d="M4.5 8.2l2.3 2.3 4.7-4.7" stroke="#fff" stroke-width="1.8" fill="none"/></svg><span>Are <b>age 10-17</b></span></li>
    <li><svg class="tick" viewBox="0 0 16 16" aria-hidden="true"><circle cx="8" cy="8" r="8" fill="#fbb816"/><path d="M4.5 8.2l2.3 2.3 4.7-4.7" stroke="#fff" stroke-width="1.8" fill="none"/></svg><span>Tend to <b>worry or overthink negative thoughts</b></span></li>
    <li><svg class="tick" viewBox="0 0 16 16" aria-hidden="true"><circle cx="8" cy="8" r="8" fill="#fbb816"/><path d="M4.5 8.2l2.3 2.3 4.7-4.7" stroke="#fff" stroke-width="1.8" fill="none"/></svg><span>Have not been <b>diagnosed with psychosis,<br>learning problems, or autism</b></span></li>
  </ul>

  <div class="compensation">
    <svg width="408" height="42" viewBox="0 0 408 42" preserveAspectRatio="none" aria-hidden="true">
      <polygon fill="#fbb816" points="0,4 30,1 60,5 90,2 120,4 150,1 180,5 210,2 240,4 270,1 300,5 330,2 360,4 390,1 408,3 405,20 408,39 380,42 350,38 320,41 290,38 260,42 230,38 200,41 170,38 140,42 110,38 80,41 50,38 20,42 2,39 4,20"/>
    </svg>
    <span>COMPENSATION UP TO $140</span>
  </div>

  <footer class="contact-bar">
    <div class="prompt"><span class="accent">Interested in participating?</span> Want more information? Please contact us!</div>
    <div class="email">solvestudy@northfield-health.org</div>
  </footer>
</main>
</body>
</html>
```